Cobalt Ridge Electric Needs A Logo Design

We need a logo for my new company based out of Sacramento, Ca called Cobalt Ridge Electric. The name says it all, my electrical contracting business provides "Cobalt Ridge Professional Work" I'm open to any colors that pop and customers to say Wow. I would love to print my cards on metal.

Industry/Entity Type

Business

Contact Information for Business Card

The card needs to have as follows
Name of company: Cobalt Ridge Electric
My Name: Marco Delvane
Phone # 916-555-0173
CL# 2049381
Email: cobaltridgeelectric@mailnest.example
and a slogan that represent "COBALT RIDGE"

Requirements
Must have
• The card needs to have as follows
• Name of company: Cobalt Ridge Electric
• My Name : Marco Delvane
• Phone # 916-555-0173
• CL# 2049381
• Email: cobaltridgeelectric@mailnest.example
• and a slogan that represent "COBALT RIDGE"
Nice to have
• popping colors
• electrical Arcing

```html
<!DOCTYPE html>
<html lang="en">
<head>
<meta charset="utf-8">
<title>Cobalt Ridge Electric – Business Card</title>
<link rel="stylesheet" href="https://fonts.googleapis.com/css2?family=Montserrat:wght@500;600;700&display=swap">
<style>
  :root {
    --backdrop: #d9d6d1;
    --card: #060606;
    --cyan: #13a8e0;
    --red: #e8443a;
  }
  * { margin: 0; padding: 0; box-sizing: border-box; }
  html, body {
    width: 1200px;
    height: 1022px;
    overflow: hidden;
    background: var(--backdrop);
  }
  .card {
    position: absolute;
    left: 100px;
    top: 225px;
    width: 1000px;
    height: 572px;
    background: var(--card);
    font-family: "Montserrat", sans-serif;
    color: var(--cyan);
  }
  .brand {
    position: absolute;
    left: 70px;
    top: 200px;
    display: flex;
    align-items: center;
    gap: 18px;
  }
  .brand-mark {
    width: 26px;
    height: 26px;
    background: var(--red);
  }
  .brand-name {
    font-size: 36px;
    font-weight: 600;
    letter-spacing: 1px;
    color: var(--cyan);
  }
  .divider {
    position: absolute;
    top: 398px;
    height: 3px;
    background: var(--red);
  }
  .divider--left { left: 0; width: 680px; }
  .divider--right { left: 968px; width: 32px; }
  .holder-name {
    position: absolute;
    left: 700px;
    top: 383px;
    width: 252px;
    font-size: 28px;
    font-weight: 700;
    letter-spacing: 1px;
    line-height: 32px;
    white-space: nowrap;
    text-align: center;
  }
  .contacts {
    position: absolute;
    left: 120px;
    top: 438px;
    list-style: none;
  }
  .contacts li {
    display: flex;
    align-items: center;
    gap: 14px;
    height: 34px;
    font-size: 24px;
    font-weight: 500;
  }
  .contacts svg {
    width: 22px;
    height: 22px;
    flex: none;
  }
</style>
</head>
<body>
  <section class="card">
    <div class="brand">
      <span class="brand-mark"></span>
      <span class="brand-name">COBALT RIDGE ELECTRIC</span>
    </div>

    <div class="divider divider--left"></div>
    <div class="holder-name">MARCO DELVANE</div>
    <div class="divider divider--right"></div>

    <ul class="contacts">
      <li>
        <svg viewBox="0 0 22 22" aria-hidden="true">
          <rect x="2" y="5" width="18" height="13" rx="1.5" fill="none" stroke="#e8443a" stroke-width="2"/>
          <line x1="6" y1="10" x2="16" y2="10" stroke="#e8443a" stroke-width="2"/>
        </svg>
        <span>2049381</span>
      </li>
      <li>
        <svg viewBox="0 0 22 22" aria-hidden="true">
          <path d="M5 3 L9 3 L10 7 L8 9 C9 12 11 14 14 15 L16 13 L20 14 L20 18 C12 19 4 11 5 3 Z" fill="#e8443a"/>
        </svg>
        <span>916-555-0173</span>
      </li>
      <li>
        <svg viewBox="0 0 22 22" aria-hidden="true">
          <rect x="2" y="5" width="18" height="13" fill="none" stroke="#e8443a" stroke-width="2"/>
          <polyline points="2,5 11,12 20,5" fill="none" stroke="#e8443a" stroke-width="2"/>
        </svg>
        <span>cobaltridgeelectric@mailnest.example</span>
      </li>
    </ul>
  </section>
</body>
</html>
```